Laser Tattoo Removal Business Cards

We are looking for a professional business card design for a laser tattoo removal business. Ideally looking for a black business card design. The name of the business is Brightline Tattoo Removal. We place our cards at local tattoo shops so we ideally are looking for something trendy/edgy to draw both male and female clientele in.

Target Market(s)

Male/Female ages 18-60

Contact Information for Business Card

black background ideally.. hoping to stay within greys, whites and black

Font styles to use
Serif
Sans Serif

Colors
121212
a9a9a9
5c5c5c
f5f5f5
ffffff
7f7f7f
606060
848484
9d9d9d

Requirements
Must have
• Employee Info:
• Melissa Thornbury
• Chief Executive Offer
• m: 919.537.2846
• w: 919.362.4178
• f: 919.685.3907
• mthornbury@brightlinetattooremoval.example
• Address:
• 4615 Oakmere Pkwy, Suite 210
• Raleigh, NC 27654
• Website:
• www.brightlinetattooremoval.example
Nice to have
• Myabe business name on back or logo on back and employee info on the front

```html
<!DOCTYPE html>
<html lang="en">
<head>
<meta charset="utf-8">
<title>Brightline Tattoo Removal – Business Card</title>
<link rel="stylesheet" href="https://fonts.googleapis.com/css2?family=Roboto+Condensed:wght@400;700&family=Roboto:wght@400&display=swap">
<style>
  :root {
    --ink: #121212;
    --paper: #f5f5f5;
    --white: #ffffff;
    --grey-dark: #5c5c5c;
    --grey-mid: #7f7f7f;
    --grey-soft: #9d9d9d;
    --grey-light: #a9a9a9;
    --backdrop: #d4d4d4;
  }
  * { margin: 0; padding: 0; box-sizing: border-box; }
  html, body { width: 1200px; height: 960px; overflow: hidden; }
  body { background: var(--backdrop); position: relative; font-family: "Roboto", Arial, sans-serif; }

  .card { position: absolute; left: 313px; width: 600px; height: 342px; }
  .card--front { top: 113px; background: var(--paper); }
  .card--back { top: 473px; background: var(--ink); }

  .wordmark { position: absolute; font-family: "Roboto Condensed", Arial, sans-serif; font-weight: 400; text-align: center; }
  .wordmark__name { display: block; font-size: 40px; letter-spacing: 3px; line-height: 1; }
  .wordmark__line { display: block; font-size: 16px; letter-spacing: 2.5px; margin-top: 14px; }
  .card--front .wordmark { right: 32px; top: 58px; width: 260px; color: #2a2a2a; }
  .card--back .wordmark { right: 40px; top: 210px; width: 240px; color: var(--white); }
  .card--back .wordmark__name { font-size: 36px; }
  .card--back .wordmark__line { font-size: 15px; margin-top: 12px; }

  .name-marker { position: absolute; left: 0; top: 172px; width: 14px; height: 36px; background: var(--ink); }
  .person { position: absolute; left: 31px; top: 172px; }
  .person__name { font-family: "Roboto Condensed", Arial, sans-serif; font-weight: 700; font-size: 21px; color: #222; line-height: 1; }
  .person__title { font-size: 15px; color: var(--grey-mid); margin-top: 4px; }

  .divider { position: absolute; left: 31px; top: 222px; width: 536px; height: 2px; background: var(--grey-mid); }

  .contacts { position: absolute; left: 31px; top: 235px; width: 290px; list-style: none; font-size: 13px; color: var(--grey-dark); }
  .contacts li { height: 19px; display: flex; align-items: center; white-space: nowrap; }
  .contacts svg { flex: none; width: 12px; height: 12px; margin-right: 9px; fill: #333; }

  .address { position: absolute; right: 32px; top: 236px; width: 225px; text-align: right; font-size: 13px; font-style: normal; color: var(--grey-dark); line-height: 19px; white-space: nowrap; }

  .edge-band { position: absolute; bottom: 0; height: 5px; }
  .edge-band--dark { left: 0; width: 392px; background: #2a2a2a; }
  .edge-band--light { left: 394px; right: 0; background: var(--grey-mid); }
</style>
</head>
<body>

<section class="card card--front" aria-label="Business card front">
  <div class="wordmark">
    <span class="wordmark__name">BRIGHTLINE</span>
    <span class="wordmark__line">TATTOO REMOVAL</span>
  </div>

  <div class="name-marker"></div>
  <div class="person">
    <p class="person__name">MELISSA THORNBURY</p>
    <p class="person__title">Chief Executive Offer</p>
  </div>

  <div class="divider"></div>

  <ul class="contacts">
    <li><svg viewBox="0 0 16 16" aria-hidden="true"><path d="M3.6 1l2.6 2.9-1.4 2c.9 1.9 2.4 3.4 4.3 4.3l2-1.4 2.9 2.6-1.5 2.4C7.6 14.6 1.4 8.4 1.2 2.5z"/></svg>919.362.4178</li>
    <li><svg viewBox="0 0 16 16" aria-hidden="true"><path d="M4 0h8a1 1 0 0 1 1 1v14a1 1 0 0 1-1 1H4a1 1 0 0 1-1-1V1a1 1 0 0 1 1-1zm1 2v10h6V2zm3 11a1 1 0 1 0 0 2 1 1 0 0 0 0-2z"/></svg>919.537.2846</li>
    <li><svg viewBox="0 0 16 16" aria-hidden="true"><path d="M4 1h8v4H4zM1 6h14v6h-2v-2H3v2H1zm3 5h8v4H4z"/></svg>919.685.3907</li>
    <li><svg viewBox="0 0 16 16" aria-hidden="true"><path d="M1 3h14v1L8 9 1 4zm0 2.5l7 5 7-5V13H1z"/></svg>mthornbury@brightlinetattooremoval.example</li>
  </ul>

  <address class="address">
    4615 Oakmere Pkwy<br>
    Suite 210<br>
    Raleigh, NC 27654<br>
    www.brightlinetattooremoval.example
  </address>

  <div class="edge-band edge-band--dark"></div>
  <div class="edge-band edge-band--light"></div>
</section>

<section class="card card--back" aria-label="Business card back">
  <div class="wordmark">
    <span class="wordmark__name">BRIGHTLINE</span>
    <span class="wordmark__line">TATTOO REMOVAL</span>
  </div>
</section>

</body>
</html>
```